High Tech Real Estate Startup needs a business card

We are developing an innovative real estate marketing product based around advanced search and virtual reality.

We talk to people, we need business cards.

Target Market(s)

The target market is technology professionals and realtors.

Contact Information for Business Card

The information to be included will include

Name
Title
Phone Number
E-mail Address
www.zelquin.com

It should use simple iconography for each one of those fields.

Font styles to use
Other font styles liked:
• Co, Jubilat, Avenir

Colors

Designer to choose colors to be used in the design.

Requirements
Must have
• Clean aesthetic,
• Good use of negative space.
• It should use our company logo, shown in the attached file. It is able to use the negative of that logo (coloured font and white background) and I have attached other acceptable accent colours in a swatch file.
Should not have
• Should not be too busy
• No extraneous text (slogans, tag lines etc)

```html
<!DOCTYPE html>
<html lang="en">
<head>
<meta charset="utf-8">
<title>Zelquin Business Card</title>
<link rel="stylesheet" href="https://fonts.googleapis.com/css2?family=Mulish:wght@400;600&display=swap">
<style>
  :root {
    --page-bg: #e6e6e4;
    --card-bg: #ffffff;
    --brand-teal: #0abbbf;
    --ink-slate: #5b6b70;
    --rule-grey: #7d8a8e;
    --card-edge: #d6d8d8;
  }
  * { margin: 0; padding: 0; box-sizing: border-box; }
  html, body {
    width: 1200px;
    height: 1000px;
    overflow: hidden;
    background: var(--page-bg);
    font-family: "Mulish", sans-serif;
  }
  .canvas { position: relative; width: 1200px; height: 1000px; }

  .card {
    position: absolute;
    background: var(--card-bg);
    border-radius: 40px;
    border: 1px solid var(--card-edge);
    overflow: hidden;
  }
  .card-front { left: 152px; top: 102px; width: 626px; height: 358px; }
  .card-back  { left: 370px; top: 545px; width: 636px; height: 363px; }

  .front-wordmark {
    position: absolute;
    left: 0; right: 0;
    top: 132px;
    text-align: center;
    color: var(--brand-teal);
    font-weight: 600;
    font-size: 78px;
    line-height: 90px;
    letter-spacing: 2px;
  }

  .back-band { position: absolute; inset: 0; }

  .back-wordmark {
    position: absolute;
    left: 542px;
    top: 180px;
    transform: translate(-50%, -50%) rotate(90deg);
    color: var(--card-bg);
    font-weight: 600;
    font-size: 50px;
    line-height: 60px;
    letter-spacing: 2px;
    white-space: nowrap;
  }

  .person-name {
    position: absolute;
    left: 38px; top: 120px;
    font-size: 32px;
    line-height: 40px;
    color: var(--ink-slate);
    font-weight: 400;
  }
  .person-title {
    position: absolute;
    left: 38px; top: 164px;
    font-size: 18px;
    line-height: 24px;
    color: var(--ink-slate);
  }
  .title-rule {
    position: absolute;
    left: 192px; top: 180px;
    width: 246px; height: 1px;
    background: var(--rule-grey);
  }

  .contact-list { position: absolute; left: 36px; top: 232px; list-style: none; }
  .contact-item {
    display: flex;
    align-items: center;
    height: 29.5px;
    font-size: 21px;
    letter-spacing: 2px;
    color: var(--ink-slate);
  }
  .contact-icon { width: 18px; height: 18px; margin-right: 22px; fill: var(--ink-slate); }
</style>
</head>
<body>
<main class="canvas">
  <section class="card card-front" aria-label="Card front">
    <div class="front-wordmark">ZELQUIN</div>
  </section>

  <section class="card card-back" aria-label="Card back">
    <svg class="back-band" width="636" height="363" viewBox="0 0 636 363" aria-hidden="true">
      <path d="M410 0 Q527 181 408 363 L636 363 L636 0 Z" fill="var(--brand-teal)"/>
    </svg>
    <div class="back-wordmark">ZELQUIN</div>

    <h1 class="person-name">Name of Person</h1>
    <p class="person-title">Title of Person</p>
    <div class="title-rule"></div>

    <ul class="contact-list">
      <li class="contact-item">
        <svg class="contact-icon" viewBox="0 0 24 24" aria-hidden="true"><path d="M6.6 10.8a15.1 15.1 0 0 0 6.6 6.6l2.2-2.2a1 1 0 0 1 1-.25 11.4 11.4 0 0 0 3.6.57 1 1 0 0 1 1 1V20a1 1 0 0 1-1 1A17 17 0 0 1 3 4a1 1 0 0 1 1-1h3.5a1 1 0 0 1 1 1c0 1.25.2 2.45.57 3.57a1 1 0 0 1-.25 1z"/></svg>
        <span>+123 456 7890</span>
      </li>
      <li class="contact-item">
        <svg class="contact-icon" viewBox="0 0 24 24" aria-hidden="true"><path d="M12 2a10 10 0 1 0 0 20 10 10 0 0 0 0-20zm6.9 6h-2.9a15.7 15.7 0 0 0-1.4-3.6A8 8 0 0 1 18.9 8zM12 4c.8 1.2 1.5 2.5 1.9 4h-3.8c.4-1.5 1.1-2.8 1.9-4zM4.3 14a8 8 0 0 1 0-4h3.4a16.5 16.5 0 0 0 0 4zm.8 2h2.9c.3 1.3.8 2.5 1.4 3.6A8 8 0 0 1 5.1 16zM8 8H5.1a8 8 0 0 1 4.3-3.6C8.8 5.5 8.3 6.7 8 8zm4 12c-.8-1.2-1.5-2.5-1.9-4h3.8c-.4 1.5-1.1 2.8-1.9 4zm2.3-6H9.7a14.7 14.7 0 0 1 0-4h4.6a14.7 14.7 0 0 1 0 4zm.3 5.6c.6-1.1 1.1-2.3 1.4-3.6h2.9a8 8 0 0 1-4.3 3.6zm1.7-5.6a16.5 16.5 0 0 0 0-4h3.4a8 8 0 0 1 0 4z"/></svg>
        <span>www.zelquin.com</span>
      </li>
      <li class="contact-item">
        <svg class="contact-icon" viewBox="0 0 24 24" aria-hidden="true"><path d="M3 5h18v14H3z M3 5l9 7 9-7" fill="var(--ink-slate)"/><path d="M3.5 5.5l8.5 6.6 8.5-6.6" fill="none" stroke="#ffffff" stroke-width="1.5"/></svg>
        <span>E-mail Address</span>
      </li>
    </ul>
  </section>
</main>
</body>
</html>
```